Brightfern Care Alliance Flirvo Ads

We want an ad created for the gay dating app flirvo. The size is 300x250. We want the ad to be sexy, with a shirtless man. We are advertising our free HIV and PrEP services. We are open to slogans about maybe "Bringing HIV and PrEP To You"
"Free PrEP and HIV Management"
Open to ideas.

We also offer through the Cedarline Relief Fund
Copay Assistance, Insurance Premium Assistance, Free Medical Services, etc
Our website is bfcanj.org

I do want the ad to have a Book Now Button

Gay sexually active males

```html
<!DOCTYPE html>
<html lang="en">
<head>
<meta charset="utf-8">
<title>Brightfern Care Alliance – Free PrEP &amp; HIV Management</title>
<link rel="stylesheet" href="https://fonts.googleapis.com/css2?family=Bebas+Neue&family=Montserrat:wght@600;700;800&display=swap">
<style>
  :root {
    --page: #9a9a9a;
    --ink: #000000;
    --white: #ffffff;
    --glow-yellow: #fff3b8;
    --glow-halo: #ffd84a;
    --hot-pink: #ff3fa4;
    --orange: #ff6500;
    --blue: #3b82ff;
    --violet: #a35cf2;
    --magenta: #f040d8;
    --coral: #ff6a6a;
    --tab-pink: #ff3f9a;
    --arc-start: #c63cf0;
    --arc-mid: #ff4fa0;
    --arc-end: #ff7a3a;
    --art-warm: #6a3a48;
    --art-cool: #4a2a66;
  }
  * { box-sizing: border-box; margin: 0; padding: 0; }
  html, body {
    width: 1200px; height: 1200px; overflow: hidden;
    background: var(--page);
  }
  .ad {
    position: absolute; left: 0; top: 89px;
    width: 1200px; height: 1022px;
    background: var(--ink);
    overflow: hidden;
    font-family: "Montserrat", sans-serif;
  }
  .arc { position: absolute; left: 0; top: 0; }
  .illustration {
    position: absolute; left: 700px; top: 60px;
    width: 500px; height: 910px;
    background: linear-gradient(160deg, var(--art-warm), var(--art-cool));
  }
  .brand-tab {
    position: absolute; left: 45px; top: -20px;
    width: 157px; height: 274px;
    border: 3px solid var(--tab-pink); border-top: none;
    border-radius: 0 0 80px 80px;
  }
  .brand-mark {
    position: absolute; left: 38px; top: 128px;
    width: 76px; height: 76px; border-radius: 50%;
    background: var(--violet);
  }
  .brand-name {
    position: absolute; left: 232px; top: 64px;
    color: var(--white);
    font-weight: 700; font-size: 38px; line-height: 1.14;
    letter-spacing: 0.06em; text-transform: uppercase;
  }
  .headline-free {
    position: absolute; left: 90px; top: 292px;
    font-family: "Bebas Neue", sans-serif; font-weight: 400;
    font-size: 232px; line-height: 1; letter-spacing: 0.01em;
    color: var(--glow-yellow);
    text-shadow: 0 0 14px var(--glow-halo), 0 0 36px rgba(255,216,74,0.55);
  }
  .headline-service {
    position: absolute; left: 86px; top: 498px;
    font-weight: 800; font-size: 88px; line-height: 1;
    color: var(--hot-pink); white-space: nowrap;
  }
  .headline-management {
    position: absolute; left: 82px; top: 610px;
    font-weight: 800; font-size: 76px; line-height: 1;
    color: var(--orange); white-space: nowrap;
  }
  .book-button {
    position: absolute; left: 64px; top: 732px;
    width: 370px; height: 65px;
    background: linear-gradient(90deg, var(--blue), var(--violet) 35%, var(--magenta) 70%, var(--coral));
    color: var(--white); text-decoration: none;
    font-weight: 700; font-size: 22px; letter-spacing: 0.22em;
    display: flex; align-items: center; justify-content: center;
  }
  .website {
    position: absolute; left: 74px; top: 844px;
    color: var(--hot-pink);
    font-weight: 600; font-size: 22px; letter-spacing: 0.3em;
  }
</style>
</head>
<body>
  <main class="ad">
    <div class="illustration" role="img" aria-label="Playful emoji-style illustration: eggplant, water droplets, peaches, hearts and sparkles"></div>

    <svg class="arc" width="1200" height="1022" viewBox="0 0 1200 1022" aria-hidden="true">
      <defs>
        <linearGradient id="arcGradient" x1="0" y1="0" x2="1" y2="0">
          <stop offset="0" stop-color="#c63cf0"/>
          <stop offset="0.5" stop-color="#ff4fa0"/>
          <stop offset="1" stop-color="#ff7a3a"/>
        </linearGradient>
      </defs>
      <path d="M100 1040 Q 633 702 1166 1040" fill="none" stroke="url(#arcGradient)" stroke-width="12"/>
    </svg>

    <div class="brand-tab"><span class="brand-mark"></span></div>
    <p class="brand-name">Brightfern<br>Care Alliance</p>

    <h1 class="headline-free">FREE</h1>
    <p class="headline-service">PrEP &amp; HIV</p>
    <p class="headline-management">MANAGEMENT</p>

    <a class="book-button" href="#">BOOK NOW!</a>
    <p class="website">WWW. BFCANJ.ORG</p>
  </main>
</body>
</html>
```